Private Investigation Business Card Design

I need a business card for a new private investigation company named Brisk Inquiries. I perform mainly surveillance jobs, vehicle repossessions, document serves etc. The final design should aim for a professional look. The logo has a magnifying glass with stick man arms and legs and is in a running action to show the "Brisk" aspect of the name. If the colour scheme could remain the same as the website www.briskinquiries-demo.com.au with silvers,blacks and a couple electric blue highlights.
Industry/Entity Type
Business
Contact Information for Business Card
Morgan Kellaway
Brisk Inquiries
0487316204
PO Box 58, Carnwell NSW 2291
info@briskinquiries-demo.com.au
www.briskinquiries-demo.com.au
Look and feel

```html
<!DOCTYPE html>
<html lang="en">
<head>
<meta charset="utf-8">
<title>Brisk Inquiries – Business Card</title>
<link rel="stylesheet" href="https://fonts.googleapis.com/css2?family=Saira:wght@400;600&family=Open+Sans:ital@1&display=swap">
<style>
  :root {
    --backdrop: #3b3b3b;
    --card-white: #fbfbfb;
    --silver-light: #d4d4d6;
    --silver-mid: #a9a8ab;
    --silver-dark: #8c8b8e;
    --ink: #1f1f1f;
    --ink-soft: #444444;
    --logo-grey: #555558;
  }
  * { margin: 0; padding: 0; box-sizing: border-box; }
  html, body {
    width: 1200px; height: 750px; overflow: hidden;
    background: var(--backdrop);
  }
  .stage {
    position: relative; width: 1200px; height: 750px;
  }
  .card {
    position: absolute; top: 228px;
    width: 461px; height: 262px;
    overflow: hidden;
  }
  .card--front { left: 124px; }
  .card--back {
    left: 618px;
    background: radial-gradient(ellipse at 50% 30%, var(--silver-light) 0%, var(--silver-mid) 75%, var(--silver-dark) 100%);
  }
  .card__shape { position: absolute; inset: 0; }

  .brand {
    position: absolute; top: 26px; right: 26px;
    display: flex; align-items: center; gap: 8px;
    font-family: "Saira", sans-serif; font-weight: 600;
    font-size: 22px; color: var(--logo-grey); letter-spacing: 0.5px;
  }
  .brand__dot {
    width: 22px; height: 22px; border-radius: 50%;
    background: var(--logo-grey);
  }

  .contact {
    position: absolute; left: 26px; top: 126px;
    font-family: "Saira", sans-serif; color: var(--ink-soft);
  }
  .contact__name {
    font-weight: 600; font-size: 17px; color: var(--ink);
    margin-bottom: 8px;
  }
  .contact__address { font-size: 11px; line-height: 14px; margin-bottom: 5px; }
  .contact__row {
    display: flex; align-items: center; gap: 7px;
    font-size: 10.5px; height: 18px;
  }
  .contact__row--phone { font-size: 12px; }
  .contact__icon { width: 11px; height: 11px; fill: var(--ink); flex: none; }

  .back-name {
    position: absolute; left: 0; right: 0; top: 88px;
    text-align: center;
    font-family: "Saira", sans-serif; font-weight: 600;
    font-size: 30px; color: var(--ink);
  }
  .back-url {
    position: absolute; left: 0; right: 0; top: 212px;
    text-align: center;
    font-family: "Open Sans", sans-serif; font-style: italic;
    font-size: 10px; letter-spacing: 3px; color: #3c3c3c;
  }
</style>
</head>
<body>
<main class="stage">

  <section class="card card--front">
    <svg class="card__shape" viewBox="0 0 461 262" width="461" height="262" aria-hidden="true">
      <defs>
        <linearGradient id="silver" x1="0" y1="0" x2="1" y2="1">
          <stop offset="0" stop-color="#b9b8bb"/>
          <stop offset="0.5" stop-color="#d9d9db"/>
          <stop offset="1" stop-color="#9e9da0"/>
        </linearGradient>
      </defs>
      <rect width="461" height="262" fill="url(#silver)"/>
      <path d="M112 0 C60 12 22 50 4 104 L0 262 L372 262 C420 245 452 210 461 166 L461 0 Z" fill="#e6e6e7"/>
      <path d="M100 0 L461 0 L461 160 C452 212 418 248 358 262 L0 262 L0 100 C18 48 52 12 100 0 Z" fill="var(--card-white)"/>
    </svg>

    <div class="brand">
      <span class="brand__name">Brisk Inquiries</span>
      <span class="brand__dot"></span>
    </div>

    <div class="contact">
      <p class="contact__name">Morgan Kellaway</p>
      <p class="contact__address">PO Box 58<br>Carnwell NSW 2291</p>
      <p class="contact__row contact__row--phone">
        <svg class="contact__icon" viewBox="0 0 24 24"><path d="M6.6 10.8a15.1 15.1 0 0 0 6.6 6.6l2.2-2.2a1 1 0 0 1 1-.25 11.4 11.4 0 0 0 3.6.57 1 1 0 0 1 1 1V20a1 1 0 0 1-1 1A17 17 0 0 1 3 4a1 1 0 0 1 1-1h3.5a1 1 0 0 1 1 1c0 1.25.2 2.45.57 3.57a1 1 0 0 1-.25 1z"/></svg>
        0487 316 204
      </p>
      <p class="contact__row">
        <svg class="contact__icon" viewBox="0 0 24 24"><path d="M2 5h20v14H2z M4 7v.5l8 5 8-5V7z" fill-rule="evenodd"/></svg>
        info@briskinquiries-demo.com.au
      </p>
      <p class="contact__row">
        <svg class="contact__icon" viewBox="0 0 24 24"><circle cx="12" cy="12" r="10"/><path d="M8 6c2 1 1 3 3 3s1 3-1 3-2 3 0 4M15 5c-1 2 1 3 2 3s2 2 1 3" stroke="#fff" stroke-width="1.6" fill="none"/></svg>
        www.briskinquiries-demo.com.au
      </p>
    </div>
  </section>

  <section class="card card--back">
    <p class="back-name">Brisk Inquiries</p>
    <p class="back-url">www.briskinquiries-demo.com.au</p>
  </section>

</main>
</body>
</html>
```